Business card design

I already have the logo design completed and am requiring business card design and layout utilising the logo. I require a front and back design.

We are an executive recruitment company so we are looking at full colour, high finish in a reasonably conservative structure.

Reason: will be provide ai template

Target Market(s)

Senior Management 35-60 age bracket

Industry/Entity Type

Business

Requirements
Must have
• Peter Welling
• Director
• 238 Morrow Tce, Kelvin Grove QLD 4059
• Ph: 07 3628 4190 Mob: 0418527306
• peter@voltinapartners.com.au
• www.voltinapartners.com.au
Nice to have
• Ideally full colour,
Should not have
• cheap looking

```html
<!DOCTYPE html>
<html lang="en">
<head>
<meta charset="utf-8">
<title>Voltina Partners – Business Card</title>
<link href="https://fonts.googleapis.com/css2?family=Open+Sans:wght@400;600;700&display=swap" rel="stylesheet">
<style>
  :root {
    --navy: #0f3a68;
    --navy-deep: #0b2b50;
    --navy-mid: #15467c;
    --accent-blue: #1f5fae;
    --ink-grey: #555a60;
    --soft-grey: #8a8d91;
    --band-grey: #9b9b9b;
    --paper: #ffffff;
    --stage: #e9e6e1;
  }
  * { box-sizing: border-box; margin: 0; padding: 0; }
  html, body { width: 900px; height: 1200px; overflow: hidden; }
  body {
    position: relative;
    background: var(--paper);
    font-family: "Open Sans", Arial, sans-serif;
  }

  /* Brand lockup */
  .brand { display: flex; align-items: center; gap: 0.45em; }
  .brand__dot {
    width: 1.6em; height: 1.6em; border-radius: 50%;
    background: var(--navy);
    flex: none;
  }
  .brand__name {
    font-weight: 700; color: var(--navy);
    letter-spacing: 0.04em; white-space: nowrap;
  }
  .brand--light .brand__dot,
  .brand--light .brand__name { color: var(--paper); }
  .brand--light .brand__dot { background: var(--paper); }

  .hero-brand {
    position: absolute; top: 0; left: 0; width: 900px; height: 222px;
    display: flex; align-items: center; justify-content: center;
    font-size: 34px;
  }

  .presentation-band {
    position: absolute; top: 222px; left: 0; width: 900px; height: 292px;
    background: var(--band-grey);
  }

  /* Card base: 388 x 215 */
  .card {
    position: absolute; width: 388px; height: 215px; overflow: hidden;
    transform-origin: top left;
  }
  .card--front { background: var(--paper); }
  .card--front .card__edge {
    position: absolute; top: 0; right: 0; width: 8px; height: 100%;
    background: linear-gradient(180deg, var(--accent-blue), var(--navy));
  }
  .card--front .brand { position: absolute; left: 32px; top: 36px; font-size: 15px; }
  .card__person { position: absolute; left: 30px; top: 113px; }
  .card__name { font-weight: 700; font-size: 15px; color: var(--navy); line-height: 1.2; }
  .card__role { font-size: 12.5px; color: var(--ink-grey); letter-spacing: 0.04em; line-height: 1.3; }
  .card__contact {
    position: absolute; left: 195px; top: 110px;
    font-size: 10.5px; line-height: 16.6px; color: var(--soft-grey);
  }

  .card--back {
    background: linear-gradient(180deg, var(--navy-mid) 0%, var(--navy) 55%, var(--navy-deep) 100%);
  }
  .card--back::after {
    content: ""; position: absolute; top: 0; right: 0; width: 10px; height: 100%;
    background: linear-gradient(90deg, rgba(0,0,0,0), rgba(0,0,0,0.35));
  }
  .card__faint-circle {
    position: absolute; left: 40px; top: 10px; width: 170px; height: 170px;
    border-radius: 50%; background: rgba(255,255,255,0.05);
  }
  .card--back .brand {
    position: absolute; left: 0; right: 0; top: 82px;
    justify-content: center; font-size: 16px;
  }
  .card__web {
    position: absolute; left: 0; right: 0; bottom: 12px; text-align: center;
    color: var(--paper); font-size: 13px; font-weight: 600; letter-spacing: 0.05em;
  }

  .band-front { left: 45px; top: 42px; }
  .band-back  { left: 470px; top: 42px; }

  .stage {
    position: absolute; top: 514px; left: 0; width: 900px; height: 686px;
    background: var(--stage);
  }
  .card--large { transform: scale(1.24); box-shadow: 0 6px 18px rgba(0,0,0,0.18); }
  .stage-back  { left: 60px;  top: 40px; }
  .stage-front { left: 360px; top: 360px; }
</style>
</head>
<body>

  <header class="hero-brand">
    <div class="brand"><span class="brand__dot"></span><span class="brand__name">VOLTINA PARTNERS</span></div>
  </header>

  <section class="presentation-band">
    <article class="card card--front band-front">
      <div class="brand"><span class="brand__dot"></span><span class="brand__name">VOLTINA PARTNERS</span></div>
      <div class="card__person">
        <p class="card__name">Peter Welling</p>
        <p class="card__role">Director</p>
      </div>
      <div class="card__contact">
        <p>238 Morrow Tce,</p>
        <p>Kelvin Grove QLD 4059</p>
        <p>P&nbsp; : 07 3628 4190</p>
        <p>M : 0418 527 306</p>
        <p>peter@voltinapartners.com.au</p>
      </div>
      <span class="card__edge"></span>
    </article>

    <article class="card card--back band-back">
      <span class="card__faint-circle"></span>
      <div class="brand brand--light"><span class="brand__dot"></span><span class="brand__name">VOLTINA PARTNERS</span></div>
      <p class="card__web">www.voltinapartners.com.au</p>
    </article>
  </section>

  <section class="stage">
    <article class="card card--back card--large stage-back">
      <span class="card__faint-circle"></span>
      <div class="brand brand--light"><span class="brand__dot"></span><span class="brand__name">VOLTINA PARTNERS</span></div>
      <p class="card__web">www.voltinapartners.com.au</p>
    </article>

    <article class="card card--front card--large stage-front">
      <div class="brand"><span class="brand__dot"></span><span class="brand__name">VOLTINA PARTNERS</span></div>
      <div class="card__person">
        <p class="card__name">Peter Welling</p>
        <p class="card__role">Director</p>
      </div>
      <div class="card__contact">
        <p>238 Morrow Tce,</p>
        <p>Kelvin Grove QLD 4059</p>
        <p>P&nbsp; : 07 3628 4190</p>
        <p>M : 0418 527 306</p>
        <p>peter@voltinapartners.com.au</p>
      </div>
      <span class="card__edge"></span>
    </article>
  </section>

</body>
</html>
```